Brightwave Reach - Business Card

We need a business card for a Social Media Marketing company that specializes in online marketing for small businesses in Canada using common Social Media platforms such as Pixlora, Chatterly, Blinkpost & Quibber.

I have uploaded a copy of our logo which I would like utilized in the business card. We would like the business card to be modern yet classy design.

Our website is www.brightwavereach.ca

Industry/Entity Type

Marketing

Contact Information for Business Card

Email: info@brightwavereach.ca
Website: www.brightwavereach.ca
Telephone: 604-555-0193

Colors

Designer to choose colors to be used in the design.

Requirements
Must have
• Social Media icons on reverse
• Please add some designs with color.

```html
<!DOCTYPE html>
<html lang="en">
<head>
<meta charset="utf-8">
<title>Brightwave Reach – Business Card</title>
<link href="https://fonts.googleapis.com/css2?family=Open+Sans:wght@400;600;700;800&display=swap" rel="stylesheet">
<style>
  :root {
    --backdrop: #d9d9d9;
    --card: #ffffff;
    --ink: #333333;
    --ink-soft: #8a8a8a;
    --rule: #444444;
    --pattern: #f1f1f1;
  }
  * { box-sizing: border-box; margin: 0; padding: 0; }
  html, body {
    width: 1200px; height: 1000px; overflow: hidden;
    background: var(--backdrop);
    font-family: "Open Sans", Arial, sans-serif;
    color: var(--ink);
  }
  .canvas { position: relative; width: 1200px; height: 1000px; }
  .card {
    position: absolute; left: 250px; width: 700px; height: 400px;
    background: var(--card);
    box-shadow: 0 6px 18px rgba(0,0,0,0.18);
  }
  .card--back { top: 60px; }
  .card--front { top: 530px; }

  .back-pattern {
    position: absolute; inset: 0;
    background: var(--pattern);
  }
  .wordmark {
    position: absolute; display: flex; align-items: center; gap: 12px;
    font-weight: 800; color: var(--ink); text-transform: uppercase;
    line-height: 1; letter-spacing: 0.5px;
  }
  .wordmark__square {
    width: 22px; height: 22px; background: var(--ink); flex: none;
  }
  .card--back .wordmark {
    left: 50%; top: 150px; transform: translateX(-50%);
    font-size: 38px; white-space: nowrap;
  }
  .social-list {
    position: absolute; left: 50%; top: 268px; transform: translateX(-50%);
    display: flex; gap: 14px; font-size: 12px; font-weight: 600;
    color: var(--ink); white-space: nowrap;
  }

  .card--front .wordmark {
    right: 50px; top: 70px; font-size: 30px; white-space: nowrap;
  }
  .person { position: absolute; left: 50px; top: 175px; }
  .person__name { font-size: 36px; font-weight: 700; letter-spacing: 1px; line-height: 1.1; }
  .person__title { font-size: 22px; font-weight: 600; color: var(--ink-soft); line-height: 1.1; }
  .divider {
    position: absolute; left: 45px; right: 80px; top: 268px;
    border-top: 1.5px solid var(--rule);
  }
  .contacts { position: absolute; left: 50px; top: 290px; list-style: none; }
  .contacts li {
    display: flex; align-items: center; gap: 14px;
    font-size: 17px; margin-bottom: 10px;
  }
  .contacts svg { width: 14px; height: 14px; fill: var(--ink); }
  .website {
    position: absolute; right: 80px; bottom: 30px; font-size: 18px; font-weight: 600;
  }
</style>
</head>
<body>
<div class="canvas">
  <section class="card card--back" aria-label="Card reverse">
    <div class="back-pattern" role="img" aria-label="Faint repeating leaf pattern background"></div>
    <div class="wordmark"><span class="wordmark__square"></span>Brightwave Reach</div>
    <ul class="social-list" style="list-style:none">
      <li>Chatterly</li><li>Quibber</li><li>Pixlora</li><li>Blinkpost</li>
    </ul>
  </section>

  <section class="card card--front" aria-label="Card front">
    <div class="wordmark"><span class="wordmark__square"></span>Brightwave Reach</div>
    <div class="person">
      <p class="person__name">DANIEL ARCHER</p>
      <p class="person__title">Precedent</p>
    </div>
    <div class="divider"></div>
    <ul class="contacts">
      <li>
        <svg viewBox="0 0 24 24" aria-hidden="true"><path d="M6.6 10.8a15 15 0 0 0 6.6 6.6l2.2-2.2c.3-.3.7-.4 1-.2 1.1.4 2.3.6 3.6.6.6 0 1 .4 1 1V20c0 .6-.4 1-1 1A17 17 0 0 1 3 4c0-.6.4-1 1-1h3.5c.6 0 1 .4 1 1 0 1.3.2 2.5.6 3.6.1.3 0 .7-.2 1z"/></svg>
        604-555-0193
      </li>
      <li>
        <svg viewBox="0 0 24 24" aria-hidden="true"><path d="M2 5h20v14H2z M2 5l10 8 10-8" fill="none" stroke="#333" stroke-width="2"/></svg>
        info@brightwavereach.ca
      </li>
    </ul>
    <p class="website">www.brightwavereach.ca</p>
  </section>
</div>
</body>
</html>
```